Milo R. Venter Birch Hollow sales specialist

I need a postcard for a mailer to a specific waterfront association, and I want to let them know I just sold THE most premier waterfront on that area, and if they are looking to sell, I am the professional they should call. The photo I uploaded I would like on the card because that is the home I sold. I would like the Phrase : Loch du Vale Sold! some place on the card, as well as all of my contact info and name of our Real Estate Firm.

Here is the name of My Firm and my contact info:\

Crandall Real Estate
Milo R. Venter
Office 555-014-3926
Cell 555-017-6248
Email Milo@crandallhomesmail.example

Industry/Entity Type

Real Estate

Font styles to use
Serif

```html
<!DOCTYPE html>
<html lang="en">
<head>
<meta charset="utf-8">
<title>Loch du Vale Sold – Postcard</title>
<link href="https://fonts.googleapis.com/css2?family=PT+Serif:ital@0;1&family=Oswald:wght@500&family=Kaushan+Script&display=swap" rel="stylesheet">
<style>
  :root {
    --paper: #ffffff;
    --ink: #1c1c1c;
    --band: #d9d9d9;
    --rule: #9a9a9a;
    --headline: #ffffff;
    --photo-sky: #c9d6e4;
    --photo-trees: #4d6b3c;
    --photo-lawn: #5f8a3e;
    --photo-path: #c98a86;
  }
  * { margin: 0; padding: 0; box-sizing: border-box; }
  html, body { width: 766px; height: 1200px; overflow: hidden; background: var(--paper); }
  .postcard { position: relative; width: 766px; height: 1200px; background: var(--paper); }

  .hero-photo {
    position: absolute; left: 0; top: 0; width: 766px; height: 604px;
    background:
      linear-gradient(180deg,
        var(--photo-sky) 0%,
        #8fa590 14%,
        var(--photo-trees) 32%,
        #6e7e62 48%,
        var(--photo-lawn) 68%,
        #8f7b66 80%,
        var(--photo-path) 92%,
        #b97d78 100%);
  }
  .hero-band { position: absolute; left: 0; top: 604px; width: 766px; height: 16px; background: var(--band); }

  .property-name {
    position: absolute; left: 294px; top: 452px;
    font-family: "Kaushan Script", cursive;
    font-size: 28px; line-height: 34px; color: var(--headline);
    text-shadow: 0 1px 3px rgba(0,0,0,.35);
    white-space: nowrap;
  }
  .sold-headline {
    position: absolute; right: 26px; top: 496px;
    font-family: "Oswald", sans-serif; font-weight: 500;
    font-size: 86px; line-height: 86px; letter-spacing: 1px;
    color: var(--headline);
  }

  .announcement {
    position: absolute; left: 67px; top: 826px; width: 280px;
    font-family: "PT Serif", serif; font-size: 15px; line-height: 21px;
    color: var(--ink);
  }
  .announcement em { font-style: italic; }
  .contact { margin-top: 21px; }

  .address-lines { position: absolute; left: 352px; top: 930px; width: 346px; }
  .address-lines span { display: block; height: 1px; background: var(--rule); margin-bottom: 43px; }
</style>
</head>
<body>
  <div class="postcard">
    <div class="hero-photo" role="img" aria-label="Photo of the sold Loch du Vale home: white lakeside house among tall pines with a lawn and curving gravel drive"></div>
    <div class="hero-band"></div>
    <div class="property-name">Birch Hollow’s Loch du Vale</div>
    <div class="sold-headline">SOLD!</div>

    <div class="announcement">
      <p>Crandall Real Estate has just<br>
      SOLD <em>Loch du Vale</em>, one of<br>
      the most prestigious homes in<br>
      Birch Hollow. If you are looking<br>
      for the current market value of<br>
      your Birch Hollow Home, or just<br>
      have Real Estate questions for<br>
      your area, please contact me,<br>
      Milo R. Venter. The Birch Hollow<br>
      Specialist.</p>
      <p class="contact">Milo R. Venter<br>
      (C) 555-017-6248<br>
      (O) 555-014-3926<br>
      (E) Milo@crandallhomesmail.example</p>
    </div>

    <div class="address-lines" aria-hidden="true"><span></span><span></span><span></span></div>
  </div>
</body>
</html>
```